Storm Restoration Contractor needs a professional letterhead design

Looking for a professional letterhead design. Not looking for your cheapo MS Word standard ones that are readily available. Dont want it to be cookie cutter look like ones readily available online. We just recently changed our logo and want to freshen up all our documents. Our company handles restoring a property back to a pre-loss condition after a storm damages it. For example, wind, hail, flood, fire losses.

Target Market(s)

Property Owners, Homeowners, Property Owners, Commercial Property Owners, Property Management Companies

Industry/Entity Type

Construction Company

Requirements
Must have
• Professional, Use 1 of 2 logo options
• Storm Restoration, Roofing, Siding, Windows

```html
<!DOCTYPE html>
<html lang="en">
<head>
<meta charset="utf-8">
<title>Stonecrest Exteriors Letterhead</title>
<link href="https://fonts.googleapis.com/css2?family=Open+Sans:wght@400;600;700&display=swap" rel="stylesheet">
<style>
  :root {
    --backdrop: #e9e9ea;
    --paper: #ffffff;
    --brand-blue: #1f7ac9;
    --brand-gray: #4a4a4d;
    --body-text: #555558;
    --watermark: #eef2f8;
  }
  * { margin: 0; padding: 0; box-sizing: border-box; }
  html, body { width: 1200px; height: 917px; overflow: hidden; }
  body {
    background: var(--backdrop);
    font-family: "Open Sans", Arial, sans-serif;
    position: relative;
  }
  .letterhead {
    position: absolute;
    left: 296px;
    top: 28px;
    width: 608px;
    height: 860px;
    background: var(--paper);
    box-shadow: 0 2px 10px rgba(0,0,0,0.12);
    overflow: hidden;
  }
  .watermark-ring {
    position: absolute;
    left: 150px;
    top: 230px;
    width: 330px;
    height: 330px;
    border: 26px solid var(--watermark);
    border-radius: 50%;
  }
  .contact-block {
    position: absolute;
    right: 40px;
    top: 40px;
    text-align: right;
    font-style: normal;
    font-size: 9px;
    line-height: 14px;
    color: var(--brand-gray);
  }
  .contact-line { display: flex; justify-content: flex-end; align-items: center; gap: 5px; }
  .contact-dot {
    width: 9px; height: 9px; border-radius: 50%;
    background: var(--brand-blue);
    display: inline-block;
  }
  .brand {
    position: absolute;
    left: 42px;
    top: 118px;
    display: flex;
    align-items: center;
    gap: 8px;
  }
  .brand-circle {
    width: 34px; height: 34px; border-radius: 50%;
    background: var(--brand-blue);
  }
  .brand-name {
    font-size: 13px;
    font-weight: 700;
    letter-spacing: 1.5px;
    color: var(--brand-blue);
    text-transform: uppercase;
  }
  .letter-body {
    position: absolute;
    left: 42px;
    top: 205px;
    width: 520px;
    font-size: 10.5px;
    line-height: 14px;
    color: var(--body-text);
  }
  .salutation {
    font-size: 13px;
    font-weight: 700;
    color: var(--brand-gray);
    margin-bottom: 8px;
  }
  .letter-body p { margin-bottom: 14px; }
  .signature {
    position: absolute;
    left: 60px;
    top: 440px;
    width: 110px;
    height: 44px;
    background: linear-gradient(90deg, #f4f4f4, #ececec);
  }
  .footer-bands {
    position: absolute;
    left: 0;
    bottom: 0;
    width: 608px;
    height: 120px;
  }
  .footer-url {
    font-family: "Open Sans", Arial, sans-serif;
    font-size: 10px;
    fill: #ffffff;
  }
</style>
</head>
<body>
  <main class="letterhead">
    <div class="watermark-ring"></div>

    <address class="contact-block">
      <div class="contact-line">2250 Harbor Ridge Rd,</div>
      <div class="contact-line">Millbrook, CA 90210 <span class="contact-dot"></span></div>
      <div class="contact-line">(555) 214-7730 <span class="contact-dot"></span></div>
      <div class="contact-line">(555) 214-7731 <span class="contact-dot"></span></div>
      <div class="contact-line">info@stonecrestexteriors.com <span class="contact-dot"></span></div>
    </address>

    <div class="brand">
      <span class="brand-circle"></span>
      <span class="brand-name">Stonecrest Exteriors</span>
    </div>

    <section class="letter-body">
      <div class="salutation">Dear Mr. Parker,</div>
      <p>Lorem Ipsum is simply dummy text of the printing and typesetting industry. Lorem Ipsum has been the industry's standard dummy text ever since the 1500s, when an unknown printer took a galley of type and scrambled it to make a type specimen book. It has survived not only five centuries, but also the leap into electronic typesetting, remaining essentially unchanged.</p>
      <p>The standard chunk of Lorem Ipsum used since the 1500s is reproduced below for those interested. Sections 1.10.32 and 1.10.33 from "Notes on Sound Roof Framing" by a master roofer are also reproduced in their exact original form, accompanied by English versions from the 1914 translation by L. Marsh.</p>
      <p>Lorem Ipsum is simply dummy text of the printing and typesetting industry. Lorem Ipsum has been the industry's standard dummy text ever since the 1500s, when an unknown printer took a galley of type and scrambled it to make a type specimen book. It has survived not only five centuries, but also the leap into electronic typesetting, remaining essentially unchanged. It was popularised in the</p>
    </section>

    <div class="signature" role="img" aria-label="Handwritten signature"></div>

    <svg class="footer-bands" viewBox="0 0 608 120" aria-hidden="true">
      <path d="M0 96 H386 C410 96 412 66 438 66 H608" fill="none" stroke="var(--brand-gray)" stroke-width="4"/>
      <path d="M0 104 H392 C418 104 420 74 446 74 H608 V100 H456 C432 100 430 114 404 114 H0 Z" fill="var(--brand-blue)"/>
      <text class="footer-url" x="590" y="91" text-anchor="end">www.stonecrestexteriors.com</text>
    </svg>
  </main>
</body>
</html>
```